****Business Card Design for Quarrystone Development. Design based around attached logo/company name

I’m looking for business card design for my company Quarrystone Development Group,LLC. Design should be professional, sharp and minimal. Outside of the attached logos, greyscale colors for remainder of cards. My thoughts are two-sided card with attached logo on one side and my info on the other but open to one-sided as well with right design.
Target Market(s)
Real estate professionals including banks, private investors, property owners, developers, commercial tenants like Brewlantern, Grovika or Tanquist’s.
Industry/Entity Type
Commercial real estate development and investments.
Contact Information for Business Card
Name, title, email, phone #’s, web address and physical address
Font styles to use
Other font styles liked:
- Helvetica, Garamond, etc
Colors
Designer to choose only greyscale colors for use in the design.
Requirements
Must have
- Attached logo first or second options.
Nice to have
- Two sided card with logo on one side. Attached Logo/company name can be laid out any way that flows as long as it’s legible.name
Should not have
- No loud colors. ***Please do not include logo, I have removed the company design with a logo image.

```html
<!DOCTYPE html>
<html lang="en">
<head>
<meta charset="utf-8">
<title>Quarrystone Development Group, LLC — Business Card</title>
<link rel="stylesheet" href="https://fonts.googleapis.com/css2?family=Cinzel:wght@400&family=Tinos:wght@400&display=swap">
<style>
  :root {
    --backdrop: #2b2b2c;
    --card-top: #1b1c1f;
    --card-bottom: #2a2b30;
    --ink-grey: #80828c;
    --ink-soft: #6f717a;
    --band-grey: #5d5f69;
    --band-dark: #202125;
    --band-shade: #45474f;
  }
  * { margin: 0; padding: 0; box-sizing: border-box; }
  html, body { width: 1200px; height: 1138px; overflow: hidden; }
  body { background: var(--backdrop); position: relative; }

  .card {
    position: absolute;
    left: 273px;
    width: 622px;
    height: 374px;
    border-radius: 14px;
    overflow: hidden;
    background: linear-gradient(160deg, var(--card-top), var(--card-bottom));
    box-shadow: 0 6px 14px rgba(0,0,0,0.45);
  }
  .card--front { top: 184px; }
  .card--back { top: 606px; }

  .company-name {
    position: absolute;
    font-family: "Cinzel", serif;
    font-weight: 400;
    color: var(--ink-grey);
    line-height: 1;
  }
  .company-name__main { display: block; font-size: 34px; letter-spacing: 1px; }
  .company-name__sub { display: block; font-size: 14px; letter-spacing: 2px; margin-top: 8px; }
  .card--front .company-name { left: 44px; top: 118px; }
  .card--back .company-name { left: 42px; top: 156px; }

  .identity {
    position: absolute;
    right: 30px;
    top: 42px;
    text-align: right;
    font-family: "Tinos", serif;
    color: var(--ink-grey);
  }
  .identity__name { font-family: "Cinzel", serif; font-size: 23px; letter-spacing: 0.5px; }
  .identity__title { font-size: 15px; margin-top: 4px; }
  .identity__address { font-size: 15px; line-height: 23px; margin-top: 11px; }

  .wave { position: absolute; left: 0; top: 0; width: 622px; height: 374px; }

  .contact {
    position: absolute;
    right: 30px;
    top: 275px;
    list-style: none;
    font-family: "Tinos", serif;
    font-size: 14px;
    color: #e4e5ea;
  }
  .contact li { display: flex; justify-content: flex-end; align-items: center; height: 22.5px; }
  .contact svg { width: 12px; height: 12px; margin-left: 10px; fill: none; stroke: #e4e5ea; stroke-width: 1.3; }
</style>
</head>
<body>

<section class="card card--front" aria-label="Card front">
  <h1 class="company-name">
    <span class="company-name__main">QUARRYSTONE</span>
    <span class="company-name__sub">DEVELOPMENT GROUP, LLC</span>
  </h1>
</section>

<section class="card card--back" aria-label="Card back">
  <svg class="wave" viewBox="0 0 622 374" aria-hidden="true">
    <path d="M0,262 C120,300 250,300 370,242 C470,196 560,186 622,196 L622,216 C560,208 470,218 380,262 C270,318 130,318 0,290 Z" fill="var(--band-shade)"/>
    <path d="M0,290 C130,318 270,318 380,262 C470,218 560,208 622,216 L622,374 L0,374 Z" fill="var(--band-grey)"/>
    <path d="M0,300 C110,330 240,334 360,292 C250,322 120,322 0,310 Z" fill="var(--band-dark)"/>
    <path d="M60,296 C170,318 290,306 390,266 C300,296 180,312 60,296 Z" fill="var(--band-dark)"/>
  </svg>

  <h2 class="company-name">
    <span class="company-name__main">QUARRYSTONE</span>
    <span class="company-name__sub">DEVELOPMENT GROUP, LLC</span>
  </h2>

  <div class="identity">
    <p class="identity__name">MARCUS HALE PORTER</p>
    <p class="identity__title">Managing Director</p>
    <p class="identity__address">418 Ledgeview Ave., Granton City,<br>Granton, US 204517</p>
  </div>

  <ul class="contact">
    <li>828-555-0147
      <svg viewBox="0 0 12 12"><path d="M2 4 Q6 1 10 4 L9 5.5 L7.5 4.8 L7.5 4 Q6 3.5 4.5 4 L4.5 4.8 L3 5.5 Z M3 7 H9 L9.5 10.5 H2.5 Z"/></svg>
    </li>
    <li>marcus@quarrystonedev.com
      <svg viewBox="0 0 12 12"><rect x="1" y="2.5" width="10" height="7"/><path d="M1 2.5 L6 6.5 L11 2.5"/></svg>
    </li>
    <li>www.quarrystonedev.com
      <svg viewBox="0 0 12 12"><circle cx="6" cy="6" r="5"/><ellipse cx="6" cy="6" rx="2.2" ry="5"/><path d="M1 6 H11"/></svg>
    </li>
  </ul>
</section>

</body>
</html>
```